Phuket Thailand - Rental Villa Website

I have a villa for rent in Thailand and require a website - i need to demo pictures/walk through video, local attractions, villa facilities description plus seaonal rates and online booking.

Industry/Entity Type

Rental

Coding

Coded - Design and coding required

```html
<!DOCTYPE html>
<html lang="en">
<head>
<meta charset="utf-8">
<title>Villa Rental – Phuket, Thailand</title>
<link href="https://fonts.googleapis.com/css2?family=Trocchi&family=Roboto:wght@400;500&display=swap" rel="stylesheet">
<style>
:root{
  --blue:#0f56c4;
  --blue-dark:#0a3f98;
  --orange:#c8470f;
  --orange-dark:#9e3406;
  --text:#6b6b6b;
  --heading:#222;
  --link:#1458c0;
  --footer:#111214;
  --footer-bottom:#0a0a0b;
  --footer-text:#8d8d8d;
  --white:#fff;
}
*{box-sizing:border-box;margin:0;padding:0}
html,body{width:1200px;height:2161px;overflow:hidden}
body{position:relative;background:var(--white);font-family:'Roboto',Arial,sans-serif;color:var(--text)}
.serif{font-family:'Trocchi',Georgia,serif}
.abs{position:absolute}

/* header */
.top-rule{left:0;top:0;width:1200px;height:3px;background:var(--orange)}
.brand{left:111px;top:28px}
.brand-name{font-family:'Trocchi',Georgia,serif;font-size:27px;color:#1a2a4a;letter-spacing:1px;line-height:1}
.brand-place{font-family:'Trocchi',Georgia,serif;font-size:13px;color:#333;margin-left:27px;margin-top:4px;letter-spacing:.5px}
.call{left:760px;top:36px;display:flex;align-items:center;gap:8px}
.call-label{font-size:10px;color:#444;letter-spacing:.3px}
.call-number{font-size:16px;color:var(--blue);margin-top:2px}
.btn-top{top:36px;height:30px;width:92px;border-radius:4px;background:linear-gradient(#d95618,var(--orange-dark));color:var(--white);font-size:11px;display:flex;align-items:center;justify-content:center;box-shadow:0 2px 3px rgba(0,0,0,.25)}

/* hero */
.hero{left:0;top:98px;width:1200px;height:560px;background:linear-gradient(110deg,#5b6a3e 0%,#414339 28%,#5b5a5e 45%,#6b4c3a 65%,#7e5842 82%,#4d3424 100%)}
.nav{left:111px;top:98px;width:978px;height:52px;background:var(--blue);display:flex}
.nav a{color:var(--white);text-decoration:none;font-size:12px;display:flex;align-items:center;justify-content:center;height:52px;flex:1 1 auto}
.nav a.active{background:var(--orange);flex:0 0 101px}
.caption{left:576px;top:410px;width:505px;height:144px;background:rgba(235,235,238,.82);border-radius:4px;padding:28px 28px 0 0;text-align:right}
.caption p{font-family:'Trocchi',Georgia,serif;font-size:15.5px;line-height:25px;color:#333;letter-spacing:.3px}
.caption-arrows{position:absolute;right:28px;top:92px;display:flex;gap:6px}

/* booking */
.booking{left:0;top:658px;width:1200px;height:144px;background:var(--blue)}
.booking h2{position:absolute;left:111px;top:20px;font-family:'Trocchi',Georgia,serif;font-weight:400;font-size:22px;color:var(--white);letter-spacing:.5px}
.field{position:absolute;top:65px;height:47px;background:var(--white);border-radius:6px;font-size:11px;color:#777;display:flex;align-items:center;justify-content:space-between;padding:0 14px;border:1px solid #c9d3e6}
.book-now{position:absolute;left:972px;top:64px;width:120px;height:47px;border-radius:5px;background:linear-gradient(#d65214,var(--orange-dark));color:var(--white);font-size:14px;display:flex;align-items:center;justify-content:center}

/* section headings */
.section-title{display:flex;align-items:center;gap:14px;font-family:'Trocchi',Georgia,serif;font-size:22px;color:var(--heading);letter-spacing:.5px}
.section-title .rule{flex:1;height:1px;background:#d8d8d8}

/* attractions */
.attractions{left:111px;top:832px;width:978px}
.attr-grid{display:flex;gap:24px;margin-top:36px}
.attr-card{width:310px}
.photo{border-radius:6px;box-shadow:0 3px 6px rgba(0,0,0,.2)}
.card-title{font-size:13.5px;line-height:20px;color:var(--link);margin-top:16px}
.card-text{font-size:11px;line-height:20px;color:var(--text);margin-top:4px}

/* about */
.about{left:0;top:1174px;width:1200px;height:285px;background:var(--blue)}
.about h2{position:absolute;left:111px;top:32px;font-family:'Trocchi',Georgia,serif;font-weight:400;font-size:22px;color:var(--white);letter-spacing:.5px}
.about p{position:absolute;left:111px;top:62px;width:645px;font-size:11.5px;line-height:26px;color:#e6edf9}
.video{position:absolute;left:785px;top:43px;width:303px;height:209px;background:var(--white);border-radius:3px;padding:5px;box-shadow:0 2px 6px rgba(0,0,0,.3)}
.video-frame{width:293px;height:170px;background:linear-gradient(120deg,#6b6f5a 0%,#5c5f66 40%,#7a5c4e 70%,#6d5547 100%)}
.video-bar{height:24px;display:flex;align-items:center;gap:4px;padding:0 2px;margin-top:4px}
.vb{height:16px;border:1px solid #ccc;border-radius:2px;background:#f3f3f3}

/* rates */
.rates{left:111px;top:1480px;width:978px}
.view-all{font-family:'Trocchi',Georgia,serif;font-size:13px;color:var(--orange);letter-spacing:.5px}
.rate-grid{display:flex;gap:26px;margin-top:30px}
.rate-card{width:225px}
.rate-row{display:flex;justify-content:space-between;align-items:center;margin-top:6px}
.price{font-family:'Trocchi',Georgia,serif;font-size:13px;color:var(--orange)}
.read-more{width:116px;height:45px;border-radius:6px;background:linear-gradient(#1d66d3,var(--blue-dark));color:var(--white);font-size:12.5px;display:flex;align-items:center;justify-content:center;margin-top:14px;box-shadow:0 2px 3px rgba(0,0,0,.3)}

/* footer */
.footer{left:0;top:1881px;width:1200px;height:224px;background:var(--footer)}
.footer h3{font-family:'Trocchi',Georgia,serif;font-weight:400;font-size:18px;color:var(--white);letter-spacing:.5px;position:absolute;top:25px}
.news-item{position:absolute;left:111px;display:flex;gap:6px}
.news-thumb{width:77px;height:53px;border:2px solid var(--orange);border-radius:5px;background:linear-gradient(120deg,#4d4138,#7a6b5c)}
.news-title{font-size:12px;color:var(--white)}
.news-text{font-size:11px;line-height:17px;color:#666;margin-top:4px}
.links{position:absolute;top:56px;font-size:11px;line-height:26px;color:#777}
.contact{position:absolute;left:662px;top:60px;font-size:11px;color:#888}
.contact-row{display:flex;gap:10px}
.social{position:absolute;left:929px;top:58px;font-size:11px;line-height:25.5px;color:#888}
.social div{display:flex;align-items:center;gap:8px}
.sq{width:12px;height:12px;border-radius:2px;display:inline-block}
.footer-bottom{left:0;top:2105px;width:1200px;height:56px;background:var(--footer-bottom);display:flex;align-items:center;justify-content:center;font-size:11px;color:#3a3a3a}
</style>
</head>
<body>

<div class="abs top-rule"></div>

<header>
  <div class="abs brand">
    <div class="brand-name">VILLA RENTAL</div>
    <div class="brand-place">PHUKET, THAILAND</div>
  </div>
  <div class="abs call">
    <svg width="26" height="26" viewBox="0 0 24 24"><path fill="#0f56c4" d="M6.6 10.8a15.2 15.2 0 0 0 6.6 6.6l2.2-2.2c.3-.3.7-.4 1-.2 1.1.4 2.3.6 3.6.6.6 0 1 .4 1 1V20c0 .6-.4 1-1 1A17 17 0 0 1 3 4c0-.6.4-1 1-1h3.5c.6 0 1 .4 1 1 0 1.3.2 2.5.6 3.6.1.3 0 .7-.2 1z"/></svg>
    <div><div class="call-label">CALL US NOW</div><div class="call-number">123 456 789</div></div>
  </div>
  <div class="abs btn-top" style="left:900px">LOGIN</div>
  <div class="abs btn-top" style="left:997px">REGISTER</div>
</header>

<section class="abs hero" role="img" aria-label="Photo of the villa exterior with garden plants and tiled roof"></section>
<nav class="abs nav">
  <a class="active">HOME</a><a>ABOUT US</a><a>LOCAL ATTRACTIONS</a><a>BOOKING</a><a>GALLERY</a><a>NEWS</a><a>CONTACT US</a><a>BLOG</a>
</nav>
<div class="abs caption">
  <p>LOREM IPSUM DOLOR SIT AMET, CONSECTETUER<br>ADIPISCING ELIT, SED DIAM NONUMMY NIBH</p>
  <div class="caption-arrows">
    <svg width="26" height="26" viewBox="0 0 26 26"><circle cx="13" cy="13" r="13" fill="#0f56c4"/><path d="M15 7l-6 6 6 6" stroke="#fff" stroke-width="3" fill="none"/></svg>
    <svg width="26" height="26" viewBox="0 0 26 26"><circle cx="13" cy="13" r="13" fill="#0f56c4"/><path d="M11 7l6 6-6 6" stroke="#fff" stroke-width="3" fill="none"/></svg>
  </div>
</div>

<section class="abs booking">
  <h2>ONLINE BOOKING</h2>
  <div class="field" style="left:111px;width:211px">Name</div>
  <div class="field" style="left:331px;width:181px">Phone</div>
  <div class="field" style="left:521px;width:183px">Where <svg width="10" height="6"><path d="M0 0h10L5 6z" fill="#888"/></svg></div>
  <div class="field" style="left:713px;width:121px">Check in <svg width="12" height="12"><rect x=".5" y="1.5" width="11" height="10" fill="none" stroke="#999"/><path d="M0 4h12M3 0v3M9 0v3" stroke="#999"/></svg></div>
  <div class="field" style="left:843px;width:121px">Check Out <svg width="12" height="12"><rect x=".5" y="1.5" width="11" height="10" fill="none" stroke="#999"/><path d="M0 4h12M3 0v3M9 0v3" stroke="#999"/></svg></div>
  <div class="book-now">BOOK NOW</div>
</section>

<section class="abs attractions">
  <div class="section-title">LOCAL ATTRACTIONS <span class="rule"></span>
    <svg width="36" height="16" viewBox="0 0 36 16"><circle cx="8" cy="8" r="8" fill="#444"/><path d="M9.5 4.5L6 8l3.5 3.5" stroke="#fff" stroke-width="2" fill="none"/><circle cx="28" cy="8" r="8" fill="#444"/><path d="M26.5 4.5L30 8l-3.5 3.5" stroke="#fff" stroke-width="2" fill="none"/></svg>
  </div>
  <div class="attr-grid">
    <article class="attr-card">
      <div class="photo" style="height:144px;background:linear-gradient(120deg,#4a3c33,#8a7d72 55%,#cfc7bd)" role="img" aria-label="Photo of a villa bedroom"></div>
      <h4 class="card-title" style="font-weight:400">Lorem ipsum dolor sit amet, consectetuer adip iscing elit, sed diam nonummy nibh</h4>
      <p class="card-text">Ut tellus dolor, dapibus eget, elementum vel, cursus eleifend, elit. Lorem ipsum dolor sit amet, consectetuer adipiscing elit. Praesent vestibulum molestie lacus.</p>
    </article>
    <article class="attr-card">
      <div class="photo" style="height:144px;background:linear-gradient(180deg,#b9bfc3,#6f7a6e 55%,#4b4a3e)" role="img" aria-label="Photo of a roofed terrace facing the hills"></div>
      <h4 class="card-title" style="font-weight:400">Duis autem vel eum iriure dolor in hendrerit in vulputate velit esse molestie</h4>
      <p class="card-text">Ut tellus dolor, dapibus eget, elementum vel, cursus eleifend, elit. Lorem ipsum dolor sit amet, consectetuer adipiscing elit. Praesent vestibulum molestie lacus.</p>
    </article>
    <article class="attr-card">
      <div class="photo" style="height:144px;background:linear-gradient(160deg,#6e8a84,#8fb5a8 50%,#4f6d66)" role="img" aria-label="Photo of the swimming pool"></div>
      <h4 class="card-title" style="font-weight:400">Eodem modo typi, qui nunc nobis videntur parum clari, fiant sollemnes in futurum</h4>
      <p class="card-text">Ut tellus dolor, dapibus eget, elementum vel, cursus eleifend, elit. Lorem ipsum dolor sit amet, consectetuer adipiscing elit. Praesent vestibulum molestie lacus.</p>
    </article>
  </div>
</section>

<section class="abs about">
  <h2>SHORTLY ABOUT US</h2>
  <p>Morbi nunc odio, gravida at, cursus nec, luctus a, lorem. Maecenas tristique orci ac sem. Duis ultricies pharetra magna. Donec accumsan malesuada orci. Donec sit amet eros. Lorem ipsum dolor sit amet, consectetuer adipiscing elit. Mauris fermentum dictum magna. Sed laoreet aliquam leo. Ut tellus dolor, dapibus eget, elementum vel, cursus eleifend, elit. Lorem ipsum dolor sit amet, consectetuer adipiscing elit. Praesent vestibulum molestie lacus. Aenean nonummy hendrerit mauris. Phasellus porta. Fusce suscipit varius mi. Lorem ipsum dolor sit amet, consecteter adipiscing elit. Praesent vestibulum molestie lacus. Morbi nunc odio, gravida at, cursus nec, luctus a, lorem. Maecenas tristique orci ac sem. Duis ultricies pharetra magna. Donec accumsan malesuada orci.</p>
  <div class="video">
    <div class="video-frame" role="img" aria-label="Walk-through video of the villa"></div>
    <div class="video-bar">
      <span class="vb" style="width:16px"></span>
      <span class="vb" style="width:38px"></span>
      <span class="vb" style="width:58px;background:linear-gradient(90deg,#f0a020 50%,#f3f3f3 50%)"></span>
      <span style="flex:1"></span>
      <span class="vb" style="width:38px"></span>
      <span class="vb" style="width:16px"></span>
      <span class="vb" style="width:16px;background:#9bd14a"></span>
    </div>
  </div>
</section>

<section class="abs rates">
  <div class="section-title">SEASONAL RATES <span class="rule"></span><span class="view-all">VIEW ALL</span></div>
  <div class="rate-grid">
    <article class="rate-card">
      <div class="photo" style="height:124px;background:linear-gradient(180deg,#b3b8bb,#6b6a5a 55%,#8c9a98)" role="img" aria-label="Photo of the terrace and hills"></div>
      <h4 class="card-title" style="font-weight:400">Lorem ipsum dolor sit amet, conse ctetuer adip</h4>
      <div class="rate-row"><svg width="62" height="12" viewBox="0 0 62 12"><g fill="#c8470f"><path id="st" d="M6 0l1.8 3.9 4.2.4-3.2 2.8 1 4.1L6 9 2.2 11.2l1-4.1L0 4.3l4.2-.4z"/><use href="#st" x="12.5"/><use href="#st" x="25"/><use href="#st" x="37.5"/><use href="#st" x="50"/></g></svg><span class="price">$.50 Per Day</span></div>
      <p class="card-text">Ut tellus dolor, dapibus eget, elementum vel, cursus eleifend, elit. Lorem ipsum dolor sit amet, consectetuer.</p>
      <div class="read-more">READ MORE</div>
    </article>
    <article class="rate-card">
      <div class="photo" style="height:124px;background:linear-gradient(150deg,#5a4a3e,#a8b2a8 50%,#6d6a5e)" role="img" aria-label="Photo of the covered veranda"></div>
      <h4 class="card-title" style="font-weight:400">Duis autem vel eum iriure dolor in hendrerit in vulputate</h4>
      <div class="rate-row"><svg width="62" height="12" viewBox="0 0 62 12"><g fill="#c8470f"><use href="#st"/><use href="#st" x="12.5"/><use href="#st" x="25"/><use href="#st" x="37.5"/><use href="#st" x="50"/></g></svg><span class="price">$.50 Per Day</span></div>
      <p class="card-text">Ut tellus dolor, dapibus eget, elementum vel, cursus eleifend, elit. Lorem ipsum dolor sit amet, consectetuer.</p>
      <div class="read-more">READ MORE</div>
    </article>
    <article class="rate-card">
      <div class="photo" style="height:124px;background:linear-gradient(120deg,#4a3c33,#8a7d72 55%,#cfc7bd)" role="img" aria-label="Photo of a bedroom"></div>
      <h4 class="card-title" style="font-weight:400">Lorem ipsum dolor sit amet, conse ctetuer adip</h4>
      <div class="rate-row"><svg width="62" height="12" viewBox="0 0 62 12"><g fill="#c8470f"><use href="#st"/><use href="#st" x="12.5"/><use href="#st" x="25"/><use href="#st" x="37.5"/><use href="#st" x="50"/></g></svg><span class="price">$.50 Per Day</span></div>
      <p class="card-text">Ut tellus dolor, dapibus eget, elementum vel, cursus eleifend, elit. Lorem ipsum dolor sit amet, consectetuer.</p>
      <div class="read-more">READ MORE</div>
    </article>
    <article class="rate-card">
      <div class="photo" style="height:124px;background:linear-gradient(180deg,#c4c8ca,#7f8a80 50%,#9fb0b0)" role="img" aria-label="Photo of the pool and lake view"></div>
      <h4 class="card-title" style="font-weight:400">Duis autem vel eum iriure dolor in hendrerit in vulputate</h4>
      <div class="rate-row"><svg width="62" height="12" viewBox="0 0 62 12"><g fill="#c8470f"><use href="#st"/><use href="#st" x="12.5"/><use href="#st" x="25"/><use href="#st" x="37.5"/><use href="#st" x="50"/></g></svg><span class="price">$.50 Per Day</span></div>
      <p class="card-text">Ut tellus dolor, dapibus eget, elementum vel, cursus eleifend, elit. Lorem ipsum dolor sit amet, consectetuer.</p>
      <div class="read-more">READ MORE</div>
    </article>
  </div>
</section>

<footer class="abs footer">
  <h3 style="left:111px">LATEST NEWS</h3>
  <div class="news-item" style="top:61px"><div class="news-thumb" role="img" aria-label="News photo of the veranda"></div><div><div class="news-title">Lorem ipsum dolor sit</div><div class="news-text">Ut wisi enim ad minim veniam,<br>quis nostrud...</div></div></div>
  <div class="news-item" style="top:138px"><div class="news-thumb" role="img" aria-label="News photo of a bedroom"></div><div><div class="news-title">Lorem ipsum dolor sit</div><div class="news-text">Ut wisi enim ad minim veniam,<br>quis nostrud...</div></div></div>

  <h3 style="left:393px">QUICK LINKS</h3>
  <div class="links" style="left:395px">Home<br>About Us<br>Villas<br>Online Bookings<br>Contact Us</div>
  <div class="links" style="left:506px">Local Attractions<br>Privacy Policy<br>Sitemap<br>Terms &amp; Conditions</div>

  <h3 style="left:662px">CONTACT US</h3>
  <div class="contact">
    <div class="contact-row"><svg width="10" height="14" viewBox="0 0 10 14"><path d="M5 0a5 5 0 0 1 5 5c0 3.5-5 9-5 9S0 8.5 0 5a5 5 0 0 1 5-5z" fill="#1c6ad8"/><circle cx="5" cy="5" r="2" fill="#111"/></svg><div style="line-height:18px">VILLA RENTAL SERVICE<br>Suite 2A, 5-7 Lorem Ipsm<br>&nbsp;Lorem Ipsm - 123 456 1765</div></div>
    <div class="contact-row" style="margin-top:12px"><svg width="14" height="10" viewBox="0 0 14 10"><rect width="14" height="10" rx="1" fill="#1c6ad8"/><path d="M0 0l7 5 7-5" stroke="#111" fill="none"/></svg><span style="font-size:12px">info@domainname.com</span></div>
    <div class="contact-row" style="margin-top:22px"><svg width="13" height="13" viewBox="0 0 24 24"><rect width="24" height="24" rx="3" fill="#1c6ad8"/><path fill="#111" d="M7 10.5a10 10 0 0 0 6.5 6.5l2-2 3 1.5V19c-7 0-13-6-13-13h3l1.5 3z"/></svg><span style="font-size:12px">123 456 789 000</span></div>
  </div>

  <h3 style="left:929px">CONNECT US</h3>
  <div class="social">
    <div><span class="sq" style="background:#3b5a9a"></span>Friendlink</div>
    <div><span class="sq" style="background:#2fa3d8"></span>Chirpnet</div>
    <div><span class="sq" style="background:#1a76b3"></span>Workmesh</div>
    <div><span class="sq" style="background:#d7452f"></span>Circleplus</div>
    <div><span class="sq" style="background:#ef7b1c"></span>RSS</div>
  </div>
</footer>
<div class="abs footer-bottom">Copyright @ 2015 Villa Rental service . All Right Reserved.</div>

</body>
</html>
```